Business Cards - New Logo Rebranding

Hello We know have a red and blue logo and are looking to create new cards. We are looking for the best creativity of the new logo merged with some of the existing artwork provided.

Target Market(s)

Realtors

Industry/Entity Type

Real Estate

Contact Information for Business Card

New logo with rebranded colors

Requirements
Must have
• Creative use of the new logo

```html
<!DOCTYPE html>
<html lang="en">
<head>
<meta charset="utf-8">
<title>Summit Crest Inspection Professionals – Business Cards</title>
<link href="https://fonts.googleapis.com/css2?family=Arimo:wght@400;700&display=swap" rel="stylesheet">
<style>
  :root {
    --stage: #3d3d3d;
    --brand-blue: #0a6fc2;
    --brand-red: #e0323c;
    --paper: #ffffff;
    --ink: #3a3a3a;
  }
  * { box-sizing: border-box; margin: 0; padding: 0; }
  html, body {
    width: 1200px; height: 803px; overflow: hidden;
    background: var(--stage);
    font-family: "Arimo", Arial, sans-serif;
  }
  .stage { position: relative; width: 1200px; height: 803px; }
  .card {
    position: absolute; top: 250px;
    width: 525px; height: 300px;
    border-radius: 22px;
    border-bottom: 4px solid var(--brand-red);
    box-shadow: 0 18px 30px rgba(0,0,0,.35);
    overflow: hidden;
  }
  .card--front { left: 45px; background: var(--brand-blue); color: var(--paper); }
  .card--back { left: 630px; background: var(--paper); color: var(--ink); }

  .brand-name {
    font-weight: 700; font-size: 26px; letter-spacing: 1px; line-height: 1;
  }
  .brand-tagline {
    font-size: 8.5px; letter-spacing: 1px; margin-top: 5px;
  }
  .brand-rule { height: 1.5px; margin-top: 5px; }

  .card--front .brand { position: absolute; left: 34px; top: 48px; width: 240px; }
  .card--front .brand-name { color: var(--paper); font-size: 24px; }
  .card--front .brand-tagline { color: var(--paper); }
  .card--front .brand-rule { background: var(--paper); }

  .person { position: absolute; left: 34px; top: 138px; }
  .person-name { font-weight: 700; font-size: 19px; }
  .person-title { font-size: 11.5px; margin-top: 3px; }

  .contacts { position: absolute; left: 34px; top: 196px; list-style: none; }
  .contacts li { display: flex; align-items: center; gap: 8px; font-size: 11.5px; line-height: 17px; }
  .contacts svg { width: 10px; height: 10px; flex: none; }

  .emblem-front {
    position: absolute; right: 34px; top: 44px;
    width: 200px; height: 200px; border-radius: 50%;
    background: var(--paper);
  }

  .card--back .emblem-back {
    position: absolute; left: 50%; top: 40px; transform: translateX(-50%);
    width: 96px; height: 96px; border-radius: 50%;
    background: var(--brand-red);
  }
  .card--back .brand { position: absolute; left: 0; right: 0; top: 150px; text-align: center; }
  .card--back .brand-name { color: var(--brand-blue); }
  .card--back .brand-tagline { color: var(--brand-blue); font-weight: 700; }
  .card--back .brand-rule { background: var(--brand-blue); width: 260px; margin: 5px auto 0; }

  .services {
    position: absolute; left: 0; right: 0; bottom: 50px;
    text-align: center; font-size: 13px; letter-spacing: .5px; color: var(--ink);
  }
</style>
</head>
<body>
<main class="stage">
  <section class="card card--front" aria-label="Business card front">
    <div class="brand">
      <div class="brand-name">SUMMIT CREST</div>
      <div class="brand-tagline">INSPECTION PROFESSIONALS</div>
      <div class="brand-rule"></div>
    </div>
    <div class="person">
      <div class="person-name">Dana Whitfield</div>
      <div class="person-title">Certified Mold Inspector</div>
    </div>
    <ul class="contacts">
      <li><svg viewBox="0 0 10 10"><path d="M2 1l2 2-1 1.2c.7 1.3 1.5 2.1 2.8 2.8L7 6l2 2-1.3 1.5C4.5 9 1 5.5.5 2.3z" fill="currentColor"/></svg>800.555.0142</li>
      <li><svg viewBox="0 0 10 10"><rect x="2.5" y=".5" width="5" height="9" rx="1" fill="none" stroke="currentColor"/></svg>562.555.0198</li>
      <li><svg viewBox="0 0 10 10"><rect x=".5" y="2" width="9" height="6" fill="none" stroke="currentColor"/><path d="M.5 2L5 5.5 9.5 2" fill="none" stroke="currentColor"/></svg>dana@summitcrestinspect.com</li>
      <li><svg viewBox="0 0 10 10"><circle cx="5" cy="5" r="4.5" fill="currentColor"/></svg>www.SummitCrestInspect.com</li>
    </ul>
    <div class="emblem-front" role="img" aria-label="Company emblem area"></div>
  </section>

  <section class="card card--back" aria-label="Business card back">
    <div class="emblem-back" role="img" aria-label="Company emblem area"></div>
    <div class="brand">
      <div class="brand-name">SUMMIT CREST</div>
      <div class="brand-tagline">INSPECTION PROFESSIONALS</div>
      <div class="brand-rule"></div>
    </div>
    <p class="services">HOME • SEWER • MOLD • COMMERCIAL • TERMITE • ROOF</p>
  </section>
</main>
</body>
</html>
```